Web Design Project - brivolta

I'm building an agency for marketing solutions but also medical education and patients education for pharmaceutical companies, medical societies and patient advocacy groups. We want to be perceived as the most innovative in the market. We work through design thinking solutions for campaigns and services.
I love some websites based on Swiss style design like www.quorlinex.com
We are a small group of designers, physicians and creatives working together to deliver the best experiences in our market.
We decided to also use pixel bazaar expecting that we maybe found a great idea we didn't thought about yet.

I'm extending it for more 2 weeks

Reason: I need the best design you can. Only PSD. No code needed. Love Swiss style, like velmora 5 and quorlinex.com I'm extending the deadline until get something great. Willing to extend as much as needed.

Target Market(s)

Pharmaceutical companies, physicians, medical societies, patients advocacy groups

Industry/Entity Type

Pharmaceutical

Font styles to use
Other font styles liked:
• Helvetia family

Colors

Designer to choose colors to be used in the design.

Requirements
Must have
• Must be innovative like www.quorlinex.com
Nice to have
• Cool menus
Should not have
• Not to appear too much Comercial. We like to be a boutique in this market. Craftsmen working with less clients at time but delivering precious stones.

```html
<!DOCTYPE html>
<html lang="en">
<head>
<meta charset="utf-8">
<title>Brivolta</title>
<link href="https://fonts.googleapis.com/css2?family=Open+Sans:ital,wght@0,400;0,600;0,700;1,400&display=swap" rel="stylesheet">
<style>
:root{
  --bg:#0d5e63;
  --tile:#137378;
  --tile-dark:#0f676c;
  --orange:#e8961e;
  --crimson:#a91c40;
  --green:#46a51f;
  --blue:#3e87f0;
  --rust:#d5472a;
  --white:#ffffff;
  --soft:#d9eeee;
}
html,body{margin:0;padding:0;background:var(--bg);overflow:hidden}
body{font-family:"Open Sans",Arial,sans-serif;color:var(--white)}
.canvas{position:relative;width:999px;height:1200px;overflow:hidden;background:var(--bg)}
.abs{position:absolute;box-sizing:border-box}
.brand{display:flex;align-items:center;gap:10px;font-weight:700;font-size:23px;letter-spacing:1.5px}
.brand-mark{width:24px;height:24px;background:var(--orange)}
.brand-mark.muted{background:#7f9a9c}
.nav{display:flex;gap:7px}
.nav-item{width:74px;height:65px;display:flex;flex-direction:column;align-items:center;justify-content:center;gap:6px;font-size:11.5px;letter-spacing:.3px}
.nav-item svg{width:18px;height:18px}
.social{left:0;top:233px;width:35px}
.social-item{height:36px;border-bottom:1px solid #0a4f53;background:var(--tile-dark);display:flex;align-items:center;justify-content:center}
.social-item span{width:22px;height:22px;border:1.5px solid #6fa6a9;border-radius:50%;box-sizing:border-box}
.photo{background:linear-gradient(135deg,#c9d3d6,#eef2f1 45%,#a9b9bd)}
.caption{left:0;right:0;bottom:0;height:46px;background:rgba(232,160,50,.88);color:#3a2a10;padding:6px 20px}
.caption h3{margin:0;font-weight:400;font-size:14px}
.caption p{margin:2px 0 0;font-size:10px}
.tile h2{margin:0;font-weight:400;font-size:16px}
.tile p{margin:0;font-size:10.4px;line-height:18.4px}
.center{display:flex;flex-direction:column;align-items:center;text-align:center}
.go{position:absolute;width:20px;height:20px}
.dots{position:absolute;display:flex;gap:3px}
.dots i{width:4px;height:4px;border-radius:50%;background:rgba(255,255,255,.45)}
.dots i:first-child{background:#0a3d40}
.footer h3{margin:0;font-weight:400;font-size:15px}
.footer p{margin:0;font-size:10.5px;line-height:18px;color:var(--soft)}
</style>
</head>
<body>
<svg width="0" height="0" style="position:absolute">
  <symbol id="go" viewBox="0 0 20 20"><circle cx="10" cy="10" r="8.6" fill="none" stroke="#fff" stroke-width="1.6"/><path d="M5.5 10h8M10.5 6.5 14 10l-3.5 3.5" fill="none" stroke="#fff" stroke-width="1.6" stroke-linecap="round" stroke-linejoin="round"/></symbol>
  <symbol id="phone" viewBox="0 0 24 24"><path d="M6 3l3 4-2 2c1 3 4 6 7 7l2-2 4 3-2 3C10 20 4 14 3 6z" fill="none" stroke="#fff" stroke-width="1.8" stroke-linejoin="round"/><path d="M14 6a4 4 0 0 1 4 4M15 2a8 8 0 0 1 7 7" fill="none" stroke="#fff" stroke-width="1.8" stroke-linecap="round"/></symbol>
</svg>

<main class="canvas">
  <header>
    <div class="abs brand" style="left:110px;top:44px"><span class="brand-mark"></span>BRIVOLTA</div>
    <nav class="abs nav" style="left:492px;top:23px">
      <div class="nav-item" style="background:var(--orange)"><svg viewBox="0 0 20 20"><path d="M2 10 10 3l8 7h-3v7h-4v-4H9v4H5v-7z" fill="#fff"/></svg>Home</div>
      <div class="nav-item" style="background:var(--crimson)"><svg viewBox="0 0 20 20"><circle cx="10" cy="6" r="4" fill="#fff"/><path d="M3 18c0-5 3-7 7-7s7 2 7 7z" fill="#fff"/></svg>About Us</div>
      <div class="nav-item" style="background:var(--green)"><svg viewBox="0 0 20 20"><circle cx="10" cy="10" r="5" fill="none" stroke="#fff" stroke-width="4" stroke-dasharray="3 1.6"/><circle cx="10" cy="10" r="2" fill="#fff"/></svg>Services</div>
      <div class="nav-item" style="background:var(--blue)"><svg viewBox="0 0 20 20"><path d="M3 9c0-4 3-6 7-6s7 2 7 6-3 6-7 6l-4 3 1-4C4 13 3 11 3 9z" fill="#fff"/><circle cx="7" cy="9" r="1" fill="var(--blue)"/><circle cx="10" cy="9" r="1" fill="var(--blue)"/><circle cx="13" cy="9" r="1" fill="var(--blue)"/></svg>Blog</div>
      <div class="nav-item" style="background:var(--rust)"><svg><use href="#phone"/></svg>Contact</div>
    </nav>
  </header>

  <aside class="abs social" aria-label="Social links">
    <div class="social-item"><span></span></div>
    <div class="social-item"><span></span></div>
    <div class="social-item"><span></span></div>
    <div class="social-item"><span></span></div>
  </aside>

  <section class="abs photo" style="left:110px;top:128px;width:398px;height:176px" role="img" aria-label="Photo of smiling pharmacists in white coats in a pharmacy">
    <svg class="go" style="right:13px;top:72px"><use href="#go"/></svg>
    <div class="abs caption"><h3>Neque porro quisquam</h3><p>Lorem ipsum dolor sit amet, consectetur adipiscing elit, sed do...</p></div>
  </section>

  <section class="abs tile" style="left:108px;top:311px;width:400px;height:215px;background:var(--tile);padding:20px 20px">
    <h2 style="font-size:18px;margin-bottom:18px">Welcome to Our Site</h2>
    <p>We are an agency for marketing solutions but also medical education and patients education for pharmaceutical companies, medical societies and patient advocacy groups.</p>
    <p style="margin-top:19px">Lorem ipsum dolor sit amet, consectetur adipiscing elit, sed do eiusmod tempor incididunt ut labore et dolore magna aliqua.</p>
    <svg class="go" style="right:20px;bottom:16px"><use href="#go"/></svg>
  </section>

  <section class="abs tile center" style="left:516px;top:129px;width:183px;height:133px;background:var(--tile);padding-top:34px">
    <svg width="36" height="34" viewBox="0 0 36 34"><rect x="6" y="2" width="28" height="30" fill="none" stroke="#fff" stroke-width="2"/><path d="M2 8v24h4" fill="none" stroke="#fff" stroke-width="2"/><rect x="11" y="7" width="18" height="6" fill="#fff"/><path d="M11 17h18M11 21h18M11 25h18" stroke="#fff" stroke-width="2"/></svg>
    <h2 style="margin-top:14px;font-size:15px">Information</h2>
  </section>

  <section class="abs tile center" style="left:707px;top:129px;width:183px;height:133px;background:var(--crimson);padding-top:34px">
    <svg width="38" height="38"><use href="#phone"/></svg>
    <h2 style="margin-top:12px;font-size:15px">Contact Us</h2>
  </section>

  <section class="abs tile center" style="left:516px;top:271px;width:183px;height:255px;background:var(--blue);padding:20px 18px 0">
    <h2 style="font-size:15px">Client Says</h2>
    <div style="width:60px;height:60px;border-radius:50%;border:2px solid #cfe0fb;margin-top:12px;background:linear-gradient(#d8dde2,#8d99a4)" role="img" aria-label="Portrait of the client"></div>
    <h2 style="font-size:12px;margin-top:14px">Tomas Revik</h2>
    <p style="font-style:italic;font-size:10px;line-height:14px">CEO, Corvane</p>
    <p style="margin-top:10px">Lorem ipsum dolor sit amet, consectetur adipiscing elit, sed do eiusmod tempor.</p>
    <div class="dots" style="right:17px;bottom:14px"><i></i><i></i><i></i><i></i></div>
  </section>

  <section class="abs tile center" style="left:707px;top:271px;width:183px;height:124px;background:var(--orange);padding-top:34px">
    <svg width="46" height="30" viewBox="0 0 46 30"><rect x="1" y="1" width="44" height="28" fill="#fff"/><path d="M1 1l22 17L45 1" fill="none" stroke="var(--orange)" stroke-width="2"/></svg>
    <h2 style="margin-top:14px;font-size:15px">News</h2>
  </section>

  <section class="abs tile center" style="left:707px;top:402px;width:183px;height:124px;background:var(--tile);padding-top:18px">
    <h2 style="font-size:15px">Partners</h2>
    <div style="width:114px;height:28px;margin-top:14px;background:#7fa7aa" role="img" aria-label="Partner badge"></div>
    <div class="dots" style="right:17px;bottom:14px"><i></i><i></i><i></i></div>
  </section>

  <section class="abs tile" style="left:108px;top:534px;width:256px;height:144px;background:var(--orange);padding:20px 16px">
    <h2 style="display:flex;align-items:center;gap:8px"><svg width="17" height="15" viewBox="0 0 17 15"><rect x="0" y="3" width="17" height="12" rx="2" fill="#fff"/><rect x="5" y="0" width="7" height="4" fill="none" stroke="#fff" stroke-width="1.6"/><path d="M8.5 6v6M5.5 9h6" stroke="var(--orange)" stroke-width="2"/></svg>Medical Education</h2>
    <p style="margin-top:12px">Lorem ipsum dolor sit amet, consectetur adipi-scing elit, sed do eiusmod tempor incididunt ut labore et dolore magna aliqua.</p>
    <svg class="go" style="right:14px;bottom:12px"><use href="#go"/></svg>
  </section>

  <section class="abs tile" style="left:371px;top:534px;width:255px;height:144px;background:var(--green);padding:20px 18px">
    <h2 style="display:flex;align-items:center;gap:8px"><svg width="22" height="22" viewBox="0 0 22 22"><circle cx="11" cy="11" r="7.5" fill="none" stroke="#fff" stroke-width="2"/><circle cx="11" cy="3" r="2.6" fill="#fff"/><circle cx="4" cy="15" r="2.6" fill="#fff"/><circle cx="18" cy="15" r="2.6" fill="#fff"/></svg>Medical Societies</h2>
    <p style="margin-top:12px">Lorem ipsum dolor sit amet, consectetur adipi-scing elit, sed do eiusmod tempor incididunt ut labore et dolore magna aliqua.</p>
    <svg class="go" style="right:14px;bottom:12px"><use href="#go"/></svg>
  </section>

  <section class="abs tile" style="left:634px;top:534px;width:256px;height:144px;background:var(--rust);padding:20px 18px">
    <h2 style="display:flex;align-items:center;gap:8px"><svg width="20" height="17" viewBox="0 0 20 17"><circle cx="6" cy="4" r="3.4" fill="#fff"/><path d="M0 15c0-5 2-7 6-7s6 2 6 7z" fill="#fff"/><circle cx="14" cy="5" r="2.8" fill="#fff"/><path d="M11 9c1-1 2-1 3-1 4 0 6 2 6 6h-7z" fill="#fff"/></svg>Patient Advocacy</h2>
    <p style="margin-top:12px">Lorem ipsum dolor sit amet, consectetur adipi-scing elit, sed do eiusmod tempor incididunt ut labore et dolore magna aliqua.</p>
    <svg class="go" style="right:16px;bottom:16px"><use href="#go"/></svg>
  </section>

  <section class="abs tile" style="left:108px;top:686px;width:256px;height:144px;background:var(--tile);padding:22px 18px">
    <h2 style="font-size:14px">Sed ut omnis iste natus</h2>
    <p style="margin-top:10px">Error sit voluptatem accusantium doloremqe laudantium, totam rem aperiam, eaque ipsasi quae ab illo inventore veritatis</p>
    <svg class="go" style="right:26px;bottom:10px"><use href="#go"/></svg>
  </section>

  <section class="abs photo" style="left:108px;top:838px;width:256px;height:144px;background:linear-gradient(110deg,#b7c1c4,#e9eeee 55%,#c3cfd2)" role="img" aria-label="Video still of a doctor beside a chart display">
    <svg class="abs" style="left:99px;top:47px" width="64" height="64" viewBox="0 0 64 64"><circle cx="32" cy="32" r="31" fill="rgba(40,40,40,.78)"/><path d="M25 17v30l24-15z" fill="#fff"/></svg>
  </section>

  <section class="abs tile center" style="left:371px;top:686px;width:255px;height:296px;background:var(--blue);padding:24px 34px 0">
    <h2 style="font-size:15px">Chirpline Feed</h2>
    <div style="width:30px;height:30px;border-radius:50%;background:#fff;margin:24px 0 26px"></div>
    <p>Sed ut <i>perspiciatis@unde omnis</i> iste natus error sit voluptatem accusantium doloremque laudantium, totam rem aperiam, eaque ipsa quae ab illo inven-tore veritatis et quasi architecto</p>
    <p style="margin-top:10px;font-style:italic">40 minutes ago</p>
    <div class="dots" style="right:22px;bottom:20px"><i></i><i></i><i></i><i></i></div>
  </section>

  <section class="abs photo" style="left:634px;top:686px;width:256px;height:144px;background:linear-gradient(120deg,#9fb0b6,#e3e6e2 50%,#b59aa2)" role="img" aria-label="Photo of a pharmacist helping a customer at a pharmacy counter"></section>

  <section class="abs tile" style="left:634px;top:838px;width:256px;height:144px;background:var(--tile);padding:22px 18px">
    <h2 style="font-size:14px">Sed ut omnis iste natus</h2>
    <p style="margin-top:10px">Error sit voluptatem accusantium doloremqe laudantium, totam rem aperiam, eaque ipsasi quae ab illo inventore veritatis</p>
    <svg class="go" style="right:18px;bottom:16px"><use href="#go"/></svg>
  </section>

  <div class="abs" style="left:108px;top:1004px;width:783px;height:5px;background:var(--tile)"></div>
  <div class="abs" style="left:108px;top:1004px;width:375px;height:5px;background:#0b5358"></div>

  <footer class="footer">
    <div class="abs brand" style="left:110px;top:1048px"><span class="brand-mark muted"></span>BRIVOLTA</div>
    <p class="abs" style="left:110px;top:1102px;font-size:10.5px;color:#fff;font-family:Arial,sans-serif">©2014. Brivolta. All Right Reserved.</p>
    <h3 class="abs" style="left:379px;top:1056px">Contact Us</h3>
    <p class="abs" style="left:381px;top:1088px">222, Street No. Building Name, City<br>State Name, ZipCode.</p>
    <p class="abs" style="left:381px;top:1141px;color:#fff">Call Us : 1800 614 902<br>Email : info@brivolta-mail.com</p>
    <h3 class="abs" style="left:646px;top:1057px">Newsletter</h3>
    <div class="abs" style="left:646px;top:1096px;width:186px;height:32px;background:var(--tile);padding:8px 15px;font-size:10.5px;color:var(--soft)">Enter your Email..</div>
    <div class="abs" style="left:834px;top:1096px;width:30px;height:32px;background:var(--tile);display:flex;align-items:center;justify-content:center"><svg width="16" height="16"><use href="#go"/></svg></div>
  </footer>
</main>
</body>
</html>
```